Road Construction Company needs business cards

We would like a new business card designed for our business.

We're a road construction company based in Qld, Australia.

Can the business card please have the following information on it.

Name: Warren Halbeck
Position: General Manager
Phone: 0472 915 348
Email: Warren.halbeck@tovrin.com.au
Address: 87 Marrow Ave, Pendlebay, QLD, 4023
Website: www.tovrin.com.au

Visually we'd like the card to be professional and simple.

Attached is our logo.

Our website is www.tovrin.com.au

Target Market(s)

Men aged 25-60

Contact Information for Business Card

As listed in project description

Font styles to use
Serif

Requirements
Must have
• Large logo on back of card

```html
<!DOCTYPE html>
<html lang="en">
<head>
<meta charset="utf-8">
<title>Tovrin Road Construction – Business Card</title>
<link href="https://fonts.googleapis.com/css2?family=Open+Sans:wght@400;600;800&display=swap" rel="stylesheet">
<style>
  :root {
    --page-bg: #e9e7e4;
    --card-bg: #1f1f23;
    --card-shadow: rgba(0, 0, 0, 0.28);
    --brand-blue: #1d5cb3;
    --accent-blue: #3aa3db;
    --text-light: #f2f2f2;
    --arrow-dark: #0c0c0e;
    --arrow-mid: #2a2a2e;
    --arrow-light: #6c6c72;
    --pattern-silver: #8a8a90;
  }
  * { box-sizing: border-box; margin: 0; padding: 0; }
  html, body {
    width: 1200px;
    height: 780px;
    overflow: hidden;
    background: var(--page-bg);
    font-family: "Open Sans", Arial, sans-serif;
  }
  .canvas {
    position: relative;
    width: 1200px;
    height: 780px;
  }
  .card {
    position: absolute;
    top: 235px;
    width: 540px;
    height: 310px;
    border-radius: 24px;
    background: var(--card-bg);
    overflow: hidden;
    box-shadow: 0 14px 30px var(--card-shadow);
  }
  .card--front { left: 40px; }
  .card--back  { left: 620px; }

  /* Shared wordmark */
  .wordmark {
    display: flex;
    align-items: center;
    gap: 10px;
    color: var(--brand-blue);
    font-weight: 800;
    letter-spacing: 3px;
    text-transform: uppercase;
    line-height: 1;
  }
  .wordmark__square {
    display: block;
    background: var(--brand-blue);
  }

  /* Front */
  .card--front .wordmark {
    position: absolute;
    left: 34px;
    top: 30px;
    font-size: 40px;
  }
  .card--front .wordmark__square { width: 14px; height: 14px; }

  .contact {
    position: absolute;
    left: 34px;
    top: 104px;
    z-index: 2;
    color: var(--text-light);
    font-size: 14.5px;
    line-height: 1.45;
    list-style: none;
  }
  .contact__address { margin-bottom: 4px; }
  .contact__item {
    display: flex;
    align-items: center;
    gap: 8px;
    white-space: nowrap;
  }
  .contact__icon {
    width: 13px;
    height: 13px;
    flex: none;
  }

  .person {
    position: absolute;
    right: 38px;
    top: 108px;
    text-align: right;
  }
  .person__name {
    color: var(--accent-blue);
    font-size: 28px;
    font-weight: 600;
    line-height: 1.15;
  }
  .person__role {
    color: var(--text-light);
    font-size: 17px;
    line-height: 1.3;
  }
  .edge-tab {
    position: absolute;
    right: 0;
    top: 114px;
    width: 16px;
    height: 58px;
    background: var(--accent-blue);
  }
  .arrow-feature {
    position: absolute;
    left: 300px;
    bottom: 0;
    width: 210px;
    height: 110px;
    background: linear-gradient(60deg, var(--arrow-dark) 0%, var(--arrow-mid) 55%, var(--arrow-light) 100%);
  }

  /* Back */
  .pattern {
    position: absolute;
    inset: 0;
    background: linear-gradient(90deg, var(--card-bg) 0%, #232327 55%, #3a3a3f 78%, var(--pattern-silver) 100%);
  }
  .card--back .wordmark {
    position: absolute;
    left: 0;
    right: 0;
    top: 50%;
    transform: translateY(-50%);
    justify-content: center;
    font-size: 74px;
    gap: 16px;
  }
  .card--back .wordmark__square { width: 24px; height: 24px; }
</style>
</head>
<body>
<main class="canvas">

  <section class="card card--front" aria-label="Business card front">
    <div class="wordmark"><span class="wordmark__square"></span>Tovrin</div>

    <ul class="contact">
      <li class="contact__address">87 Marrow Ave,<br>Pendlebay, QLD, 4023</li>
      <li class="contact__item">
        <svg class="contact__icon" viewBox="0 0 16 16" aria-hidden="true">
          <path d="M3.5 1.5l2.5 0 1.2 3.2-1.6 1.2c.9 1.9 2.4 3.4 4.3 4.3l1.2-1.6 3.2 1.2v2.5c0 .9-.8 1.7-1.7 1.7C6.9 14 2 9.1 1.8 3.2c0-.9.8-1.7 1.7-1.7z" fill="var(--accent-blue)"/>
        </svg>
        <span>0472 915 348</span>
      </li>
      <li class="contact__item">
        <svg class="contact__icon" viewBox="0 0 16 16" aria-hidden="true">
          <rect x="1" y="3" width="14" height="10" rx="1.5" fill="var(--accent-blue)"/>
          <path d="M1.5 4l6.5 5 6.5-5" fill="none" stroke="var(--card-bg)" stroke-width="1.4"/>
        </svg>
        <span>www.tovrin.com.au</span>
      </li>
      <li class="contact__item">
        <svg class="contact__icon" viewBox="0 0 16 16" aria-hidden="true">
          <circle cx="8" cy="8" r="7" fill="var(--accent-blue)"/>
          <path d="M1 8h14M8 1c2.5 2.5 2.5 11.5 0 14M8 1c-2.5 2.5-2.5 11.5 0 14" fill="none" stroke="var(--card-bg)" stroke-width="1"/>
        </svg>
        <span>Warren.halbeck@tovrin.com.au</span>
      </li>
    </ul>

    <div class="person">
      <p class="person__name">Warren Halbeck</p>
      <p class="person__role">General Manager</p>
    </div>
    <span class="edge-tab"></span>

    <div class="arrow-feature" role="img" aria-label="Large glossy black arrowhead shape pointing upward"></div>
  </section>

  <section class="card card--back" aria-label="Business card back">
    <div class="pattern" role="img" aria-label="Rows of small arrowhead shapes fading from black to silver toward the right"></div>
    <div class="wordmark"><span class="wordmark__square"></span>Tovrin</div>
  </section>

</main>
</body>
</html>
```